Premium CBD/Hemp company needs packaging and label design

Quillmore Apothecare, a premium CBD/Hemp company based in Scottsdale, Arizona is in need of a packaging and label design. We are launching with our flagship product which will be a 30 count capsule and will come in three functions: Pain Relief, Anxiety Support, and Sleep Support. For the purpose of this contest, please design packaging and label for our Anxiety Support product. Our products are physician formulated and all natural. Our main ingredient is CBD/Hemp and is complemented by specific herbs that synergistically work together to give the customer the most effective and desired result. We would like our branding to have a pharmaceutical look and feel with a focus on trust and transparency. We have uploaded our company logo that is to be used on both the packaging and label. We have also uploaded an executed branding questionnaire that will guide you to exactly what we are seeking to achieve as to the look and feel of our brand. Please feel free to contact us with any questions that you may have. The winner of this contest will have the opportunity to work with us on future projects as we will need packaging and label design for our entire Quillmore Apothecare product line.

Target Market(s)

See attached branding questionnaire

Industry/Entity Type

Health And Wellness

Font styles to use
Sans Serif

Colors

Designer to choose colors to be used in the design.

Requirements
Must have
• See attached branding questionnaire; Please superimpose labels onto a cobalt blue capsule bottle (see attached)
• >>UPON REVIEW of the FIRST 8 designs, we really like the silver, mildly metallic label background in DESIGN # 21300528, we do not want metalic lettering as that would not look very "Pharmaceutical"
• >>We are in search of a look that is a bit more "Pharmaceutical" than a look that would be more commonly found in a Supplement Store
Nice to have
• "See attached branding questionnaire
Should not have
• See attached branding questionnaire; NO marijuana or cannabis plant on the packaging or label

```html
<!DOCTYPE html>
<html lang="en">
<head>
<meta charset="utf-8">
<title>Quillmore Apothecare – Anxiety Support Carton</title>
<link href="https://fonts.googleapis.com/css2?family=Open+Sans:wght@400;600;800&display=swap" rel="stylesheet">
<style>
  :root {
    --brand-green: #1f984a;
    --leaf-green: #45a964;
    --navy: #233a94;
    --silver: #b9b9bb;
    --silver-light: #e4e4e6;
    --silver-dark: #9a9a9c;
    --body-grey: #6d6e71;
    --panel-grey: #d1d2d3;
    --white: #ffffff;
  }
  * { margin: 0; padding: 0; box-sizing: border-box; }
  html, body {
    width: 1200px; height: 1200px; overflow: hidden;
    background: var(--white);
    font-family: "Open Sans", Arial, sans-serif;
  }
  .canvas { position: relative; width: 1200px; height: 1200px; }

  .lid-panel {
    position: absolute; left: 300px; top: 143px; width: 353px; height: 277px;
    background: var(--brand-green);
  }
  .front-panel {
    position: absolute; left: 300px; top: 422px; width: 674px; height: 608px;
  }
  .front-panel svg { display: block; }

  .wordmark {
    position: absolute; display: flex; align-items: center; gap: 10px;
    font-weight: 600; text-transform: uppercase; letter-spacing: 2px; line-height: 1.15;
  }
  .wordmark .dot { border-radius: 50%; border: 2px solid currentColor; flex: none; }
  .wordmark--lid { left: 352px; top: 248px; color: var(--silver-light); font-size: 21px; }
  .wordmark--lid .dot { width: 68px; height: 68px; }
  .wordmark--band { left: 724px; top: 480px; color: var(--silver-light); font-size: 15px; }
  .wordmark--band .dot { width: 46px; height: 46px; }
  .wordmark--front { left: 401px; top: 656px; color: var(--navy); font-size: 16px; }
  .wordmark--front .dot { width: 48px; height: 48px; }

  .product-title {
    position: absolute; left: 340px; top: 774px; width: 300px; text-align: center;
  }
  .product-title .name {
    display: block; color: var(--navy); font-weight: 800; font-size: 50px;
    letter-spacing: -0.5px; line-height: 1;
  }
  .product-title .function {
    display: block; color: var(--brand-green); font-weight: 400; font-size: 22px;
    letter-spacing: 2px; margin-top: 4px;
  }
  .tagline {
    position: absolute; left: 340px; top: 871px; width: 300px; text-align: center;
    font-size: 12px; color: var(--body-grey); letter-spacing: 1px;
  }
  .count {
    position: absolute; left: 500px; top: 982px; width: 116px; text-align: center;
    font-size: 11px; color: var(--body-grey); letter-spacing: 1px;
  }
  .description {
    position: absolute; left: 715px; top: 640px; width: 210px;
    font-size: 12px; line-height: 15.6px; color: var(--body-grey);
  }
  .info-box {
    position: absolute; left: 715px; top: 865px; width: 203px; height: 112px;
    background: var(--panel-grey);
  }
</style>
</head>
<body>
<div class="canvas">
  <div class="lid-panel"></div>
  <div class="wordmark wordmark--lid"><span class="dot"></span><span>Quillmore<br>Apothecare</span></div>

  <div class="front-panel">
    <svg width="674" height="608" viewBox="375 528 843 760" xmlns="http://www.w3.org/2000/svg">
      <defs>
        <linearGradient id="silverSweep" x1="0" y1="0" x2="1" y2="0">
          <stop offset="0" stop-color="#c7c7c9"/>
          <stop offset="0.5" stop-color="#f1f1f2"/>
          <stop offset="1" stop-color="#a8a8aa"/>
        </linearGradient>
        <linearGradient id="leafWash" x1="0" y1="0" x2="1" y2="1">
          <stop offset="0" stop-color="#3aa55c"/>
          <stop offset="0.5" stop-color="#1f984a"/>
          <stop offset="1" stop-color="#3aa55c"/>
        </linearGradient>
      </defs>
      <rect x="375" y="528" width="843" height="760" fill="#ffffff"/>
      <path class="silver-swoosh" fill="url(#silverSweep)"
        d="M375,820 C470,750 620,700 790,700 C960,700 1100,740 1218,765 V777 C1100,752 960,716 790,716 C600,716 420,780 392,950 C380,1080 440,1190 522,1287 H375 Z"/>
      <path class="green-band" fill="url(#leafWash)" role="img" aria-label="Band of soft falling leaves on green"
        d="M375,528 H1218 V768 C1100,740 960,702 790,702 C620,702 470,745 375,813 Z"/>
    </svg>
  </div>

  <div class="wordmark wordmark--band"><span class="dot"></span><span>Quillmore<br>Apothecare</span></div>
  <div class="wordmark wordmark--front"><span class="dot"></span><span>Quillmore<br>Apothecare</span></div>

  <div class="product-title">
    <span class="name">ANXIETY</span>
    <span class="function">SUPPORT</span>
  </div>
  <p class="tagline">Lorem ipsum Lorem ipsumLorem</p>
  <p class="count">30 TABLETS</p>

  <p class="description">Lorem ipsum Lorem ipsumLorem ipsum Lorem ipsumLorem ipsum Lorem ipsumLorem ipsum Lorem ipsumLorem ipsum Lorem ipsumLorem ipsum Lorem ipsumLorem ipsum Lorem ipsumLorem ipsum Lorem ipsumLorem ipsum Lorem ipsumLorem ipsum Lorem ipsumLorem ipsum Lorem ipsumLorem ipsum Lorem ipsumLorem ipsum Lorem ipsumLorem ipsum Lorem ipsumLorem ipsum Lorem ipsum</p>
  <div class="info-box"></div>
</div>
</body>
</html>
```